"Vine Hollow Excursions" is a top notch Santa Barbara County Wine Tour company.

We provide scenic, boutique and custom wine tours. I need the card to be clean and classy. I will provide our logo. I would like the logo to cover the back side of the card as an option and would like to see a couple color options other then our signature green and gold. I would like to see some creative options and let the designers come up with options.
I need cards for myself and my team. The final design should communicate "An authentic and boutique wine tour experience"
Please use my website for reference www.vinehollowexcursions.example

Target Market(s)

We have a wide range of clients from millennials to baby boomers

Industry/Entity Type

Tour

Contact Information for Business Card

Contact info:
Dale Morton
805-219-6384
info@vinehollowexcursions.example
vinehollowexcursions.example

Colors

Designer to choose colors to be used in the design.

Requirements
Must have
• my logo
Nice to have
• *I would like to have the backside side with the logo and the company statement
• "An authentic and boutique wine tour experience" as an option.
• *I would also like to see what the designers can create!
• *I would like to see an option that incorporates or social: instagram, yelp, trip advisor
Should not have
• I do not want it too busy.

```html
<!DOCTYPE html>
<html lang="en">
<head>
<meta charset="utf-8">
<title>Vine Hollow Excursions — Business Card</title>
<link href="https://fonts.googleapis.com/css2?family=Cinzel:wght@400;500&family=Montserrat:wght@300;400&display=swap" rel="stylesheet">
<style>
  :root {
    --backdrop: #4a443f;
    --vine-green: #2f6b45;
    --vine-green-deep: #1f5a36;
    --card-white: #ffffff;
    --gold: #a48c72;
    --ink-grey: #6f6f6f;
    --ink-green: #2c5f3d;
  }
  * { box-sizing: border-box; margin: 0; padding: 0; }
  html, body {
    width: 1200px; height: 930px; overflow: hidden;
    background: var(--backdrop);
  }
  .stage { position: relative; width: 1200px; height: 930px; }

  .card {
    position: absolute;
    width: 660px; height: 377px;
    box-shadow: 0 10px 28px rgba(0,0,0,0.35);
    overflow: hidden;
  }

  /* Back side */
  .card-back {
    left: 70px; top: 50px;
    background: linear-gradient(135deg, #3d7a52 0%, var(--vine-green) 55%, #2a6340 100%);
    display: flex; align-items: center; justify-content: center;
  }
  .brand-lockup {
    display: flex; align-items: center; gap: 16px;
    color: var(--card-white);
  }
  .brand-dot {
    width: 18px; height: 18px; border-radius: 50%;
    background: var(--card-white);
  }
  .brand-name {
    font-family: 'Cinzel', serif; font-weight: 400;
    font-size: 34px; letter-spacing: 2px;
  }

  /* Front side */
  .card-front {
    left: 470px; top: 500px;
    background: var(--card-white);
  }
  .vineyard-rows {
    position: absolute; inset: 0;
    background:
      radial-gradient(ellipse 70% 85% at 70% 0%, #ffffff 0%, #ffffff 45%, rgba(255,255,255,0) 75%),
      linear-gradient(160deg, #ffffff 0%, #ffffff 40%, #6f9c7e 65%, var(--vine-green-deep) 100%);
  }
  .card-front .brand-name {
    position: absolute; right: 34px; top: 58px;
    color: var(--gold); font-size: 22px; letter-spacing: 1.5px;
  }
  .contact-block {
    position: absolute; left: 44px; top: 110px;
    font-family: 'Montserrat', sans-serif; font-weight: 300;
    color: var(--ink-grey); font-size: 14px; line-height: 22px;
  }
  .person-name {
    font-family: 'Cinzel', serif; font-weight: 400;
    color: var(--ink-green); font-size: 24px; line-height: 30px;
  }
  .person-role { margin-bottom: 8px; }
  .contact-line { display: flex; align-items: center; gap: 10px; }
  .contact-line svg { width: 12px; height: 12px; fill: none; stroke: var(--ink-green); stroke-width: 1.6; }
</style>
</head>
<body>
<div class="stage">
  <section class="card card-back">
    <div class="brand-lockup">
      <span class="brand-dot"></span>
      <span class="brand-name">Vine Hollow Excursions</span>
    </div>
  </section>

  <section class="card card-front">
    <div class="vineyard-rows" role="img" aria-label="Vineyard rows fanning out toward a bright horizon in green and white"></div>
    <span class="brand-name">Vine Hollow Excursions</span>
    <div class="contact-block">
      <div class="person-name">Dale Morton</div>
      <div class="person-role">Founder</div>
      <div>418 Alder Row</div>
      <div>Fenwick, MO 63099</div>
      <div class="contact-line">
        <svg viewBox="0 0 12 12"><path d="M2 1.5 L4 1.5 L5 4 L3.8 5 Q5 7.5 7 8.2 L8 7 L10.5 8 L10.5 10 Q5 11 1.5 3 Z"/></svg>
        <span>805-219-6384</span>
      </div>
      <div class="contact-line">
        <svg viewBox="0 0 12 12"><rect x="1" y="2.5" width="10" height="7"/><path d="M1 2.5 L6 6.5 L11 2.5"/></svg>
        <span>info@vinehollowexcursions.example</span>
      </div>
      <div class="contact-line">
        <svg viewBox="0 0 12 12"><circle cx="6" cy="6" r="4.8"/><path d="M1.2 6 H10.8 M6 1.2 Q3 6 6 10.8 M6 1.2 Q9 6 6 10.8"/></svg>
        <span>www.vinehollowexcursions.example</span>
      </div>
    </div>
  </section>
</div>
</body>
</html>
```